Harborlight Amusement Collective (HAC)

We need a business card design for Harborlight Amusement Collective. Modern and sleek looking, with all critical information. Open to single or double sided designs, if double sided info needs to be all on one side. The main Logo is Harborlight Amusement collective and must be on the card. The other three logos are for the brands that fall under the group, they might be good on the back.

Industry/Entity Type

Business

```html
<!DOCTYPE html>
<html lang="en">
<head>
<meta charset="utf-8">
<title>Harborlight Amusement Collective – Business Card</title>
<link href="https://fonts.googleapis.com/css2?family=Montserrat:wght@400;500;600;700&display=swap" rel="stylesheet">
<style>
  :root {
    --blue: #2356a1;
    --green: #8aa93a;
    --ink: #222831;
    --white: #ffffff;
    --backdrop: #dcdcdc;
    --rule: #c9d69a;
  }
  * { box-sizing: border-box; margin: 0; padding: 0; }
  html, body { width: 1200px; height: 852px; overflow: hidden; }
  body {
    background: var(--backdrop);
    font-family: "Montserrat", sans-serif;
    color: var(--ink);
    position: relative;
  }
  .card {
    position: absolute;
    top: 269px;
    width: 550px;
    height: 314px;
    background: var(--white);
    border-radius: 22px;
    overflow: hidden;
  }
  .card--brands { left: 35px; }
  .card--contact { left: 615px; }

  /* group name block */
  .group-name {
    display: flex;
    flex-direction: column;
    align-items: center;
    gap: 10px;
  }
  .group-name__mark {
    width: 58px; height: 58px;
    background: var(--blue);
    border-radius: 6px;
  }
  .group-name__text {
    font-weight: 700;
    color: var(--blue);
    text-transform: uppercase;
    text-align: center;
    line-height: 1.25;
    letter-spacing: 1px;
  }

  /* brands side */
  .card--brands .group-name { position: absolute; top: 28px; left: 0; right: 0; }
  .card--brands .group-name__text { font-size: 19px; }
  .rule {
    position: absolute; left: 40px; right: 40px; height: 1.5px;
    background: var(--rule);
  }
  .rule--top { top: 178px; }
  .rule--bottom { top: 270px; }
  .brands-label {
    position: absolute; top: 188px; left: 0; right: 0;
    text-align: center; font-size: 12px; font-weight: 500;
  }
  .brand-list {
    position: absolute; top: 212px; left: 0; right: 0;
    display: flex; justify-content: center; align-items: center;
  }
  .brand {
    font-size: 17px; font-weight: 700; color: var(--blue);
    display: flex; align-items: center; gap: 7px;
    padding: 0 18px;
  }
  .brand + .brand { border-left: 1.5px solid #b8b8b8; }
  .brand__dot { width: 14px; height: 14px; border-radius: 50%; background: var(--green); }
  .brand__dot--blue { background: var(--blue); }
  .site {
    position: absolute; top: 280px; left: 0; right: 0;
    text-align: center; font-size: 12px; font-weight: 500;
  }

  /* contact side */
  .wave { position: absolute; inset: 0; width: 550px; height: 314px; }
  .card--contact .group-name { position: absolute; top: 30px; left: 20px; width: 300px; }
  .card--contact .group-name__text { font-size: 17px; }
  .person { position: absolute; top: 26px; right: 28px; text-align: right; }
  .person__name { font-size: 20px; font-weight: 700; color: var(--blue); }
  .person__role { font-size: 12px; font-weight: 500; margin-top: 3px; }
  .contact-list {
    position: absolute; top: 150px; right: 26px;
    list-style: none; color: var(--white);
    font-size: 12.5px; text-align: right; line-height: 1.5;
  }
  .contact-list li { display: flex; justify-content: flex-end; align-items: center; gap: 7px; }
  .contact-list svg { width: 12px; height: 12px; fill: var(--white); flex: none; }
  .contact-list .no-icon { padding-right: 19px; }
</style>
</head>
<body>

<section class="card card--brands">
  <div class="group-name">
    <span class="group-name__mark"></span>
    <span class="group-name__text">Harborlight Amusement<br>Collective</span>
  </div>
  <div class="rule rule--top"></div>
  <p class="brands-label">Our Brands</p>
  <div class="brand-list">
    <span class="brand"><span class="brand__dot"></span>HarborPass</span>
    <span class="brand">Tribune Hosting</span>
    <span class="brand"><span class="brand__dot brand__dot--blue"></span>seatmark</span>
  </div>
  <div class="rule rule--bottom"></div>
  <p class="site">www.harborlightcollective.com</p>
</section>

<section class="card card--contact">
  <svg class="wave" viewBox="0 0 550 314" aria-hidden="true">
    <path d="M550,81 C400,86 330,126 280,176 C230,226 150,254 0,258 L0,314 L550,314 Z" fill="var(--green)"/>
    <path d="M550,89 C400,94 330,134 280,184 C230,234 150,262 0,266 L0,314 L550,314 Z" fill="var(--white)"/>
    <path d="M550,95 C400,100 330,140 280,190 C230,240 150,268 0,272 L0,314 L550,314 Z" fill="var(--blue)"/>
  </svg>
  <div class="group-name">
    <span class="group-name__mark"></span>
    <span class="group-name__text">Harborlight Amusement<br>Collective</span>
  </div>
  <div class="person">
    <p class="person__name">Mara Ellison</p>
    <p class="person__role">Managing Director</p>
  </div>
  <ul class="contact-list">
    <li class="no-icon">88 Lantern Quay,</li>
    <li>Bayview, US 402190
      <svg viewBox="0 0 24 24"><path d="M12 2C8 2 5 5 5 9c0 5 7 13 7 13s7-8 7-13c0-4-3-7-7-7zm0 9.5A2.5 2.5 0 1 1 12 6.5a2.5 2.5 0 0 1 0 5z"/></svg></li>
    <li>555.014.2290
      <svg viewBox="0 0 24 24"><path d="M6.6 10.8a15 15 0 0 0 6.6 6.6l2.2-2.2c.3-.3.7-.4 1-.2 1.1.4 2.3.6 3.6.6.6 0 1 .4 1 1V20c0 .6-.4 1-1 1A17 17 0 0 1 3 4c0-.6.4-1 1-1h3.5c.6 0 1 .4 1 1 0 1.3.2 2.5.6 3.6.1.3 0 .7-.2 1z"/></svg></li>
    <li>mara@harborlightcollective.com
      <svg viewBox="0 0 24 24"><path d="M2 5h20v14H2zm2 2v.5l8 5 8-5V7z"/></svg></li>
    <li>www.harborlightcollective.com
      <svg viewBox="0 0 24 24"><path d="M12 2a10 10 0 1 0 0 20 10 10 0 0 0 0-20zm6.9 6h-3a15 15 0 0 0-1.3-3.6A8 8 0 0 1 18.9 8zM12 4c.8 1.2 1.5 2.5 1.9 4h-3.8c.4-1.5 1.1-2.8 1.9-4zM4.3 14a8 8 0 0 1 0-4h3.4a16 16 0 0 0 0 4zm.8 2h3a15 15 0 0 0 1.3 3.6A8 8 0 0 1 5.1 16zm3-8h-3a8 8 0 0 1 4.3-3.6C8.9 5.5 8.4 6.7 8.1 8zM12 20c-.8-1.2-1.5-2.5-1.9-4h3.8c-.4 1.5-1.1 2.8-1.9 4zm2.3-6H9.7a14 14 0 0 1 0-4h4.6a14 14 0 0 1 0 4zm.3 5.6c.6-1.1 1-2.3 1.3-3.6h3a8 8 0 0 1-4.3 3.6zm1.7-5.6a16 16 0 0 0 0-4h3.4a8 8 0 0 1 0 4z"/></svg></li>
  </ul>
</section>

</body>
</html>
```